New homepage and Product page - Lumen Vq

Reason: I have narrowed it done to 3 designers and just need to get the designs revised

Industry/Entity Type

Product

```html
<!DOCTYPE html>
<html lang="en">
<head>
<meta charset="utf-8">
<title>Lumen Vq — Green Coffee Bean</title>
<link href="https://fonts.googleapis.com/css2?family=Questrial&family=Mulish:wght@400;600;700;800&display=swap" rel="stylesheet">
<style>
:root{
  --green-top:#5aae00;
  --green-deep:#3f8a00;
  --green-mid:#5fae0e;
  --green-light:#8fd42a;
  --green-text:#4b8a1c;
  --green-link:#5c9a12;
  --tag-lime:#b8e24a;
  --arrow:#7fc423;
  --ink:#555;
  --ink-soft:#666;
  --panel-a:#f7f7f3;
  --panel-b:#e3e1da;
  --footer:#e9e5df;
  --rule:#cfc9bd;
  --brown:#5c5046;
  --gold:#e3a70f;
  --white:#fff;
}
*{box-sizing:border-box;margin:0;padding:0}
html,body{width:1200px;height:1000px;overflow:hidden;background:var(--white)}
body{position:relative;font-family:"Mulish",Arial,sans-serif;color:var(--ink)}
.abs{position:absolute}
.heading{font-family:"Questrial","Mulish",sans-serif;font-weight:400}

/* header */
.top-line{left:0;top:0;width:1200px;height:3px;background:var(--green-top)}
.site-header{left:0;top:3px;width:1200px;height:64px;background:linear-gradient(#fff,#ececec)}
.main-nav{left:241px;top:30px;display:flex;gap:38px;font-size:11.5px;font-weight:700;color:var(--ink)}
.logo-tab{left:468px;top:30px;width:266px;height:62px}
.brand{left:500px;top:18px;width:200px;height:50px;display:flex;align-items:center;justify-content:center;gap:8px;font-family:"Questrial",sans-serif;font-size:29px;color:#1f6b35}
.brand-dot{width:13px;height:13px;border-radius:50%;background:#6bbf2a}
.phone{right:250px;top:24px;font-size:19px;color:var(--ink);font-weight:400}

/* hero */
.hero{left:0;top:67px;width:1200px;height:373px;background:radial-gradient(ellipse 420px 260px at 650px 160px,var(--green-light),var(--green-mid) 60%,var(--green-deep) 100%);overflow:hidden}
.beans-art{left:595px;top:155px;width:140px;height:260px;border-radius:60px 40px 30px 70px;background:radial-gradient(ellipse at 60% 55%,rgba(143,182,87,.9),rgba(95,138,48,.6) 60%,rgba(95,138,48,0) 100%)}
.script-line{left:387px;top:342px;width:200px;height:34px;border-radius:6px;background:linear-gradient(90deg,rgba(200,240,110,.35),rgba(200,240,110,.12))}
.tagline{left:0;top:103px;width:1200px;text-align:center;font-size:13px;font-weight:700;color:var(--tag-lime);letter-spacing:.3px}
.hero-title{left:241px;top:162px;font-size:35px;color:var(--white);letter-spacing:.3px;white-space:nowrap}
.hero-copy{left:241px;top:220px;width:345px;font-size:12.5px;line-height:17.6px;font-weight:700;color:var(--white)}
.btn-more{left:242px;top:338px;width:131px;height:37px;border:3px solid var(--white);border-radius:4px;background:#566c2b;color:var(--white);font-size:15px;display:flex;align-items:center;justify-content:center;gap:8px;font-family:"Questrial",sans-serif}
.btn-more span{color:var(--tag-lime);font-weight:800}
.product-box{left:727px;top:131px;width:210px;height:270px;border-radius:3px;background:linear-gradient(#fff 0,#fff 30%,#1d7a3a 30%,#1d7a3a 40%,#f1c325 40%,#f1c325 55%,#3b8f2a 55%,#3b8f2a 90%,#eee 90%);box-shadow:0 4px 10px rgba(0,0,0,.25)}
.hero-arrow{top:231px;width:37px;height:37px;background:var(--arrow);color:#2f4d10;font-size:16px;font-weight:800;display:flex;align-items:center;justify-content:center}
.arrow-left{left:0;border-radius:0 4px 4px 0}
.arrow-right{left:1163px;border-radius:4px 0 0 4px}
.hero-bump{left:530px;top:425px;width:140px;height:16px}
.dots{left:580px;top:434px;display:flex;gap:5px}
.dots i{width:10px;height:4px;border-radius:2px;background:#ddd}
.dots i.on{background:var(--green-text)}

/* intro */
.intro-title{left:0;top:477px;width:1200px;text-align:center;font-size:30px;color:var(--green-text)}
.intro-copy{left:290px;top:516px;width:620px;text-align:center;font-size:16px;line-height:23px;color:var(--ink-soft)}

/* features */
.features{left:242px;top:597px;width:715px;height:202px;border:1px solid #ddd;background:linear-gradient(90deg,var(--panel-a),var(--panel-b))}
.features-bar{left:242px;top:597px;width:385px;height:30px;background:var(--green-deep);color:var(--white);font-size:16px;padding:6px 0 0 17px;font-family:"Questrial",sans-serif}
.person-photo{left:618px;top:575px;width:152px;height:224px;border-radius:70px 70px 0 0;background:linear-gradient(#4a3428 0,#7a5646 35%,#d8b59a 70%,#e9d2c0)}
.feature{left:258px;width:350px}
.feature h3{font-size:12.5px;font-weight:700;color:#555;display:flex;align-items:center;gap:6px}
.feature h3 i{width:17px;height:17px;border-radius:0 10px 0 10px;background:#7cc62a;display:inline-block}
.feature p{margin:4px 0 0 24px;font-size:10.8px;line-height:16.5px;color:var(--ink-soft)}
.leaves-art{left:725px;top:585px;width:135px;height:115px;border-radius:50%;background:radial-gradient(#8ad13a,rgba(138,209,58,0) 70%)}
.guarantee-seal{left:857px;top:610px;width:80px;height:80px;border-radius:50%;background:radial-gradient(#f6c531,var(--gold));border:3px solid #f7d56b}
.guarantee-copy{left:770px;top:703px;width:175px;font-size:11px;line-height:17px;color:var(--ink-soft)}
.guarantee-copy b{color:#555}

/* badges row */
.tested-seal{left:241px;top:826px;width:52px;height:52px;border-radius:50%;background:var(--brown)}
.badge-copy{font-size:10px;line-height:16px;color:var(--ink-soft)}
.tested-copy{left:306px;top:830px;width:280px}
.tested-copy a{color:var(--green-link);font-weight:700;text-decoration:none}
.usa-seal{left:615px;top:829px;width:50px;height:50px}
.usa-copy{left:677px;top:828px;width:270px}
.usa-copy b{color:#555;font-size:11px}

/* footer */
.site-footer{left:0;top:904px;width:1200px;height:96px;background:var(--footer)}
.footer-rule{left:242px;top:904px;width:716px;height:1px;background:var(--rule)}
.copyright{left:241px;top:925px;font-size:9px;line-height:17px;color:var(--ink-soft)}
.copyright b{color:#555}
.footer-nav{left:723px;top:931px;font-size:9px;font-weight:700;color:var(--green-link)}
.footer-nav span{color:#999;margin:0 4px;font-weight:400}
.social{left:876px;top:925px;display:flex;gap:8px}
.social i{width:22px;height:22px;border-radius:3px;background:#8f8b85}
</style>
</head>
<body>
<div class="abs top-line"></div>
<header class="abs site-header"></header>
<nav class="abs main-nav"><span>Home</span><span>Products</span><span>Contact Us</span></nav>

<section class="abs hero"></section>
<svg class="abs logo-tab" viewBox="0 0 266 62" aria-hidden="true"><path d="M0 37 C30 37 40 55 70 58 L196 58 C226 55 236 37 266 37 L266 0 L0 0 Z" fill="#fff"/></svg>
<div class="abs brand"><span class="brand-dot"></span>Lumen Vq</div>
<div class="abs phone">1 800 555 0142</div>

<div class="abs beans-art" role="img" aria-label="Green coffee beans and leaves"></div>
<div class="abs script-line" role="img" aria-label="Hand-lettered line: Effective Weight Loss"></div>
<div class="abs tagline">A BRAND YOU CAN TRUST</div>
<h1 class="abs hero-title heading">GREEN COFFEE BEAN</h1>
<p class="abs hero-copy">Lumen Vq Green Coffee Bean is made with 100% pure natural ingredients. Unlike other products, Lumen Vq Green Coffee Bean is made with premium green coffee bean that supplies 45% chlorogenic acid, which is the active weight-loss component of green coffee bean.</p>
<div class="abs btn-more">LEARN MORE <span>›</span></div>
<div class="abs product-box" role="img" aria-label="Green Coffee Bean product box, two bottle bonus pack"></div>
<div class="abs hero-arrow arrow-left">‹</div>
<div class="abs hero-arrow arrow-right">›</div>
<svg class="abs hero-bump" viewBox="0 0 140 16" aria-hidden="true"><path d="M0 16 C20 16 20 3 45 2 L95 2 C120 3 120 16 140 16 Z" fill="#fff"/></svg>
<div class="abs dots"><i class="on"></i><i></i><i></i></div>

<h2 class="abs intro-title heading">THE BEST OF NATURE &amp; SCIENCE</h2>
<p class="abs intro-copy">New Lumen Vq is line of natural, high-quality, weight-loss supplements that are scientifically formulated for better efficiency!</p>

<section class="abs features"></section>
<div class="abs features-bar">ALL OUR PRODUCTS ARE</div>
<div class="abs person-photo" role="img" aria-label="Photo of a smiling woman"></div>
<div class="abs feature" style="top:645px"><h3><i></i>100% PURE NATURAL INGREDIENTS</h3><p>Lumen Vq products are made with 100% pure natural ingredients. Unlike other products, Lumen Vq products are made with premium natural ingredients for effective results.</p></div>
<div class="abs feature" style="top:727px"><h3><i></i>SCIENTIFICALLY FORMULATED</h3><p>Lumen Vq products are scientifically formulated to deliver the exact clinically tested doses that are needed to see results!</p></div>
<div class="abs leaves-art" role="img" aria-label="Sprig of green leaves"></div>
<div class="abs guarantee-seal" role="img" aria-label="Money back guarantee seal"></div>
<p class="abs guarantee-copy"><b>Lumen Vq is guaranteed to work or your money back.</b> Simply return it to the place of purchase within 30 days for a refund with original receipt.</p>

<div class="abs tested-seal" role="img" aria-label="Clinically tested seal"></div>
<p class="abs badge-copy tested-copy">Lorem ipsum dolor sit amet, consectetur adipisicing elit, sed do eiusmod incididunt ut labore et dolore magna aliqua enim ad minim laboris nisi ut aliquip ext ... <a>Find out more</a></p>
<svg class="abs usa-seal" viewBox="0 0 50 50" role="img" aria-label="Made in USA seal"><path d="M3 3 H47 V28 L25 48 L3 28 Z" fill="#6b6b6b"/><path d="M8 30 H42 L25 45 Z" fill="#a9a9a9"/></svg>
<p class="abs badge-copy usa-copy"><b>Made in the USA</b><br>Lumen Vq is manufactured in a GMP-compliant manufacturing facility to ensure 100% quality.</p>

<footer class="abs site-footer"></footer>
<div class="abs footer-rule"></div>
<p class="abs copyright">© Copyright 2014 Corvel Studio<br>Website by <b>Corvel Studio</b></p>
<nav class="abs footer-nav">Home<span>|</span>Products<span>|</span>Contact Us</nav>
<div class="abs social"><i></i><i></i><i></i></div>
</body>
</html>
```